Business card for a Exhibition booth fabrication company

Hi. My company would like to change our corporate name card. We are an events and Exhibition stand builder company. We would like our corporate name card to resonate what we do. I need someone to create something unique that relates to the industry that I am in. The graphic designer should be creative to incorporate the elements of my industry and try to blend in well in the design of the card. Our aim is to ensure that we are unique and our card can look different from our competitors.
Updates

Target Market(s)

Marketing and events manager from all companies

Contact Information for Business Card

The business card should have the following details:
Name
Job Title
Email
Website

Colors

Designer to choose colors to be used in the design.

Requirements
Must have
• The card must be look something that is relevant to the service that I am providing. My website is: www.velmora-buildworks.com
• You can see my website to get more information on what service that I am doing
Nice to have
• On the back of my card, I would like to have a globe image with the incorporation of my company logo. This is to indicate that my services can be done in any part of the world.

```html
<!DOCTYPE html>
<html lang="en">
<head>
<meta charset="utf-8">
<title>Velmora Buildworks – Business Card</title>
<link rel="stylesheet" href="https://fonts.googleapis.com/css2?family=Montserrat:wght@500;600;700&family=PT+Serif:ital,wght@0,400;1,700&display=swap">
<style>
  :root {
    --bg: #e7e4df;
    --card-white: #ffffff;
    --charcoal: #323232;
    --slate: #444446;
    --red: #e21f26;
    --deep-red: #8c0d12;
    --ink: #3a3a3a;
    --soft-grey: #d9d9d9;
    --text-light: #f2f2f2;
  }
  * { box-sizing: border-box; margin: 0; padding: 0; }
  html, body { width: 1200px; height: 1200px; overflow: hidden; }
  body { background: var(--bg); position: relative; font-family: "PT Serif", serif; }

  .card {
    position: absolute; left: 130px; width: 940px; height: 537px;
    background: var(--card-white);
    box-shadow: 0 6px 18px rgba(0,0,0,0.18);
    overflow: hidden;
  }
  .card--back { top: 40px; }
  .card--front { top: 623px; }
  .card-shapes { position: absolute; inset: 0; }

  /* Back side */
  .globe-area {
    position: absolute; left: 150px; top: 40px; width: 640px; height: 460px;
    border-radius: 50% 50% 46% 46%;
    background: radial-gradient(ellipse at 55% 45%, #e2e2e2 0%, #ececec 45%, rgba(255,255,255,0) 72%);
  }
  .brand {
    position: absolute; display: flex; align-items: center; gap: 16px;
    font-family: "Montserrat", sans-serif; font-weight: 600;
    color: var(--ink); letter-spacing: 3px; white-space: nowrap;
  }
  .brand-dot { width: 34px; height: 34px; border-radius: 50%; background: var(--red); flex: none; }
  .card--back .brand { left: 50%; top: 50%; transform: translate(-50%, -50%); font-size: 40px; }
  .card--front .brand { left: 500px; top: 205px; font-size: 27px; }
  .card--front .brand-dot { width: 26px; height: 26px; }

  /* Front side */
  .identity { position: absolute; left: 52px; top: 44px; }
  .identity-name {
    font-family: "Montserrat", sans-serif; font-weight: 600; font-size: 36px;
    letter-spacing: 1px; display: flex; align-items: center; gap: 14px;
  }
  .identity-name .marker {
    width: 0; height: 0; border-top: 14px solid transparent; border-bottom: 14px solid transparent;
    border-left: 22px solid var(--red);
  }
  .first-name { color: var(--red); }
  .last-name { color: var(--text-light); }
  .job-title { font-family: "PT Serif", serif; font-weight: 700; font-style: italic; color: #cfcfcf; font-size: 20px; margin: 2px 0 0 36px; }
  .rule { width: 300px; height: 2px; background: var(--red); margin: 18px 0 0 36px; }

  .contacts { position: absolute; left: 40px; top: 196px; list-style: none; }
  .contacts li { display: flex; align-items: center; gap: 12px; color: var(--text-light); font-size: 21px; margin-bottom: 10px; }
  .contacts svg { width: 26px; height: 26px; flex: none; }

  .address {
    position: absolute; left: 440px; top: 452px; color: #fff;
    font-size: 20px; line-height: 1.25; display: flex; align-items: center; gap: 16px;
  }
  .address svg { width: 24px; height: 30px; }
</style>
</head>
<body>

<section class="card card--back" aria-label="Card back">
  <div class="globe-area" role="img" aria-label="Faint grey world map"></div>
  <div class="brand"><span class="brand-dot"></span>VELMORA BUILDWORKS</div>
</section>

<section class="card card--front" aria-label="Card front">
  <svg class="card-shapes" viewBox="0 0 940 537" aria-hidden="true">
    <polygon points="0,0 520,0 420,537 0,537" fill="var(--charcoal)"/>
    <polygon points="520,0 640,0 440,130 500,0" fill="var(--red)"/>
    <polygon points="0,420 230,420 230,537 0,537" fill="var(--slate)"/>
    <rect x="230" y="420" width="110" height="117" fill="var(--deep-red)"/>
    <polygon points="350,420 700,420 700,537 350,537" fill="var(--red)"/>
  </svg>

  <div class="identity">
    <div class="identity-name"><span class="marker"></span><span class="first-name">DAREN</span><span class="last-name">KOLE</span></div>
    <div class="job-title">Director</div>
    <div class="rule"></div>
  </div>

  <ul class="contacts">
    <li>
      <svg viewBox="0 0 26 26"><polygon points="13,1 24,7 24,19 13,25 2,19 2,7" fill="none" stroke="var(--red)" stroke-width="2"/><path d="M9 8 l3 0 l1 3 l-2 1 a7 7 0 0 0 3 3 l1-2 l3 1 l0 3 a9 9 0 0 1 -9 -9z" fill="var(--red)"/></svg>
      (123) 000-418
    </li>
    <li>
      <svg viewBox="0 0 26 26"><polygon points="13,1 24,7 24,19 13,25 2,19 2,7" fill="none" stroke="var(--red)" stroke-width="2"/><rect x="7" y="9" width="12" height="9" fill="none" stroke="var(--red)" stroke-width="1.6"/><path d="M7 9 l6 5 l6-5" fill="none" stroke="var(--red)" stroke-width="1.6"/></svg>
      username@velmora-buildworks.com
    </li>
    <li>
      <svg viewBox="0 0 26 26"><polygon points="13,1 24,7 24,19 13,25 2,19 2,7" fill="none" stroke="var(--red)" stroke-width="2"/><circle cx="13" cy="13" r="6" fill="none" stroke="var(--red)" stroke-width="1.6"/><path d="M7 13h12M13 7v12" stroke="var(--red)" stroke-width="1.4"/></svg>
      www.velmora-buildworks.com
    </li>
  </ul>

  <div class="brand"><span class="brand-dot"></span>VELMORA BUILDWORKS</div>

  <div class="address">
    <span>4120 Harbor Lane 210<br>Austin, TX 73301</span>
    <svg viewBox="0 0 24 30"><path d="M12 2a8 8 0 0 0-8 8c0 6 8 14 8 14s8-8 8-14a8 8 0 0 0-8-8z" fill="none" stroke="#fff" stroke-width="2.4"/><circle cx="12" cy="10" r="3" fill="#fff"/><path d="M5 28h14" stroke="#fff" stroke-width="2.4"/></svg>
  </div>
</section>

</body>
</html>
```